Fitness Business Card Design Needed

We are looking for a business card design that stands out but is also simple and unique. I like the idea of on one side using the picture of myself with my logo at my feet. I love the texture on the business card so please take that into account when designing. Then on the other side having my contact details. I want it to be clean, modern, and pretty. I am open to designs that allow spot gloss or gold foiling.

Contact Information for Business Card

Space for Name, Phone number, email, and website

```html
<!DOCTYPE html>
<html lang="en">
<head>
<meta charset="utf-8">
<title>PocketPower Fitness – Business Card</title>
<link rel="stylesheet" href="https://fonts.googleapis.com/css2?family=Roboto:wght@400;500;700&display=swap">
<style>
  :root {
    --backdrop: #2b2b2c;
    --card-white: #ffffff;
    --card-dark: #3d3d3f;
    --gold: #b88a3c;
    --gold-light: #d9b56a;
    --ink: #2f2f2f;
    --rule: #8a8a8a;
    --strip: #3a3a3a;
    --logo-light: #f2f2f2;
  }
  * { box-sizing: border-box; margin: 0; padding: 0; }
  html, body {
    width: 1200px; height: 801px; overflow: hidden;
    background: var(--backdrop);
    font-family: "Roboto", Arial, sans-serif;
  }
  .stage { position: relative; width: 1200px; height: 801px; }
  .card {
    position: absolute; top: 246px;
    width: 540px; height: 309px; overflow: hidden;
    box-shadow: 0 10px 24px rgba(0,0,0,.45);
  }
  /* Contact side */
  .card--front { left: 620px; background: var(--card-white); color: var(--ink); }
  .brand {
    position: absolute; right: 36px; top: 44px;
    display: flex; flex-direction: column; align-items: center; gap: 12px;
  }
  .brand__square { width: 38px; height: 38px; border: 2px solid var(--gold); }
  .brand__name {
    font-weight: 400; font-size: 15px; letter-spacing: 3px;
    color: var(--ink); text-transform: uppercase;
  }
  .person { position: absolute; left: 40px; top: 112px; }
  .person__name {
    font-weight: 700; font-size: 24px; color: var(--gold);
    text-transform: uppercase; letter-spacing: .5px;
  }
  .person__role { font-size: 15px; text-transform: uppercase; margin-top: 2px; }
  .divider {
    position: absolute; left: 36px; right: 36px; top: 176px;
    height: 1px; background: var(--rule);
  }
  .contact { position: absolute; left: 40px; top: 190px; font-size: 14px; }
  .contact__row { display: flex; align-items: center; gap: 9px; height: 22px; }
  .contact__row svg { width: 12px; height: 12px; fill: var(--gold); }
  .address {
    position: absolute; right: 36px; top: 222px;
    text-align: right; font-size: 15px; line-height: 20px;
  }
  .band { position: absolute; left: 0; bottom: 0; width: 540px; height: 44px; }
  .website {
    position: absolute; right: 36px; bottom: 10px;
    font-size: 15px; font-weight: 500; letter-spacing: .8px; color: var(--ink);
  }
  /* Portrait side */
  .card--back { left: 40px; background: var(--card-dark); }
  .portrait {
    position: absolute; left: 222px; top: 28px; width: 96px; height: 214px;
    border-radius: 40px 40px 6px 6px;
    background: linear-gradient(180deg, #d8c6a4 0%, #c98f72 30%, #d0583f 48%, #c88a6c 70%, #c9ae86 100%);
  }
  .back-brand {
    position: absolute; left: 0; right: 0; top: 252px;
    display: flex; flex-direction: column; align-items: center;
  }
  .back-brand__name {
    font-weight: 400; font-size: 17px; letter-spacing: 3px;
    color: var(--logo-light); text-transform: uppercase;
    padding: 0 8px 4px; border-bottom: 1px solid var(--logo-light);
  }
</style>
</head>
<body>
<div class="stage">

  <section class="card card--back">
    <div class="portrait" role="img" aria-label="Full-length photo of the trainer standing on a small mound of sand"></div>
    <div class="back-brand">
      <span class="back-brand__name">PocketPower Fitness</span>
    </div>
  </section>

  <section class="card card--front">
    <div class="brand">
      <span class="brand__square"></span>
      <span class="brand__name">PocketPower Fitness</span>
    </div>

    <div class="person">
      <h1 class="person__name">Lena Ortiz</h1>
      <p class="person__role">Fitness Trainer</p>
    </div>

    <div class="divider"></div>

    <div class="contact">
      <div class="contact__row">
        <svg viewBox="0 0 24 24"><path d="M6.6 10.8a15 15 0 006.6 6.6l2.2-2.2a1 1 0 011-.25 11.4 11.4 0 003.6.57 1 1 0 011 1V20a1 1 0 01-1 1A17 17 0 013 4a1 1 0 011-1h3.5a1 1 0 011 1c0 1.25.2 2.45.57 3.57a1 1 0 01-.25 1z"/></svg>
        <span>555 014 2290</span>
      </div>
      <div class="contact__row">
        <svg viewBox="0 0 24 24"><path d="M2 5h20v14H2z M2 5l10 8 10-8" /></svg>
        <span>info@pocketpowerfit.com</span>
      </div>
    </div>

    <address class="address" style="font-style:normal">
      1420 Juniper Court<br>Willow Bend, Alaska 99512
    </address>

    <svg class="band" viewBox="0 0 540 44" preserveAspectRatio="none">
      <defs>
        <linearGradient id="goldFoil" x1="0" x2="1" y1="0" y2="0">
          <stop offset="0" stop-color="var(--gold)"/>
          <stop offset=".55" stop-color="var(--gold-light)"/>
          <stop offset="1" stop-color="var(--gold)"/>
        </linearGradient>
      </defs>
      <rect x="0" y="34" width="260" height="10" fill="var(--strip)"/>
      <polygon points="250,44 290,6 540,6 540,44" fill="url(#goldFoil)"/>
    </svg>
    <span class="website">www.pocketpowerfit.com</span>
  </section>

</div>
</body>
</html>
```